TalkHarbor - Language Coaching Services

Sleek, innovative, trendy design for Language Coaching business.

TalkHarbor is a new UK based company that provides Language Coaching services. We offer highly personalized on-line and face to face language courses. We also impart learning techniques workshops based on the latest neuroscience research for second-language acquisition.

Target Market(s)

See attached info

Industry/Entity Type

Consulting

Contact Information for Business Card

TalkHarbor
DaniaKV@talkharbor.co.uk
TalkHarbor.co.uk
London, UK

Font styles to use
Sans Serif

```html
<!DOCTYPE html>
<html lang="en">
<head>
<meta charset="utf-8">
<title>TalkHarbor – Business Card</title>
<link href="https://fonts.googleapis.com/css2?family=Exo+2:wght@400;500;600&display=swap" rel="stylesheet">
<style>
  :root {
    --backdrop: #2a2a2c;
    --card-dark-top: #3a3839;
    --card-dark-bottom: #1f1d1e;
    --brand-blue: #1a9fd4;
    --brand-blue-light: #29b3e6;
    --brand-blue-deep: #0a86bd;
    --text-light: #f2f2f2;
  }
  * { box-sizing: border-box; margin: 0; padding: 0; }
  html, body {
    width: 1200px; height: 900px; overflow: hidden;
    background: var(--backdrop);
    font-family: "Exo 2", Arial, sans-serif;
  }
  .stage {
    position: relative; width: 1200px; height: 900px;
    display: flex; justify-content: center; align-items: center; gap: 60px;
  }
  .card {
    width: 350px; height: 620px; position: relative;
    box-shadow: 0 18px 40px rgba(0,0,0,.45);
  }
  /* front */
  .card-front {
    background: linear-gradient(160deg, var(--card-dark-top), var(--card-dark-bottom));
    color: var(--text-light);
    display: flex; flex-direction: column; align-items: center;
    padding: 44px 30px 0;
  }
  .front-name {
    align-self: flex-start;
    color: var(--brand-blue);
    font-size: 30px; font-weight: 500; letter-spacing: 1.5px;
    text-transform: uppercase;
  }
  .front-mark {
    width: 230px; height: 230px; margin-top: 30px;
    border: 14px solid var(--brand-blue); border-radius: 50%;
  }
  .company {
    margin-top: 36px; color: var(--brand-blue);
    font-size: 23px; font-weight: 600;
  }
  .icons { display: flex; gap: 14px; margin-top: 14px; }
  .icons svg { width: 20px; height: 20px; fill: var(--brand-blue); }
  .contact {
    list-style: none; text-align: center; margin-top: 12px;
    font-size: 16px; line-height: 1.65;
  }
  .contact .address { color: var(--brand-blue); }
  .rule {
    position: absolute; left: 26px; right: 26px; bottom: 40px;
    height: 1px; background: var(--brand-blue);
  }
  /* back */
  .card-back {
    background: radial-gradient(circle at 40% 35%, var(--brand-blue-light), var(--brand-blue-deep));
    color: #fff;
    display: flex; flex-direction: column; align-items: center; justify-content: center;
    padding-bottom: 40px;
  }
  .back-mark {
    width: 110px; height: 110px;
    border: 7px solid #fff; border-radius: 50%;
  }
  .back-name {
    margin-top: 22px; font-size: 34px; font-weight: 500;
    letter-spacing: 1.5px; text-transform: uppercase;
  }
  .back-url { margin-top: 6px; font-size: 14px; font-weight: 500; }
</style>
</head>
<body>
<main class="stage">
  <section class="card card-front">
    <h1 class="front-name">TalkHarbor</h1>
    <div class="front-mark" aria-hidden="true"></div>
    <h2 class="company">TalkHarbor</h2>
    <div class="icons" aria-hidden="true">
      <svg viewBox="0 0 20 20"><path d="M5 2l3 4-2 2c1 2 3 4 5 5l2-2 4 3-2 3C9 17 3 11 2 4z"/></svg>
      <svg viewBox="0 0 20 20"><path d="M2 5h16v10H2z M2 5l8 6 8-6" stroke="#2b292a" stroke-width="1.5"/></svg>
      <svg viewBox="0 0 20 20"><circle cx="10" cy="10" r="8"/><path d="M2 10h16M10 2c-4 4-4 12 0 16M10 2c4 4 4 12 0 16" stroke="#2b292a" stroke-width="1.2" fill="none"/></svg>
      <svg viewBox="0 0 20 20"><path d="M10 1a6 6 0 0 1 6 6c0 5-6 12-6 12S4 12 4 7a6 6 0 0 1 6-6z"/><circle cx="10" cy="7" r="2.3" fill="#2b292a"/></svg>
    </div>
    <ul class="contact">
      <li>+44 1632 960817</li>
      <li>DaniaKV@talkharbor.co.uk</li>
      <li>www.TalkHarbor.co.uk</li>
      <li class="address">14 Harbour Row, EC1A 4ZZ,<br>London, UK</li>
    </ul>
    <div class="rule"></div>
  </section>

  <section class="card card-back">
    <div class="back-mark" aria-hidden="true"></div>
    <p class="back-name">TalkHarbor</p>
    <p class="back-url">www.TalkHarbor.co.uk</p>
  </section>
</main>
</body>
</html>
```